holloway paving service

Needs to have phone number 0418259730 and email markholloway@brightmail.com.au.
ABN 62318470915
name mark holloway

For all your concreting solutions
Excavation
Exposed & colour concrete
House & shed slabs
Driveways
Landing & steps

Contact Information for Business Card

ph 0418259730
email markholloway@brightmail.com.au.
ABN 62318470915
name mark holloway

```html
<!DOCTYPE html>
<html lang="en">
<head>
<meta charset="utf-8">
<title>Holloway Paving Service – Business Card</title>
<link rel="stylesheet" href="https://fonts.googleapis.com/css2?family=Lato:wght@400;700&family=Montserrat:wght@600&display=swap">
<style>
  :root {
    --orange: #ec6a1f;
    --grey-dark: #4a4a4a;
    --grey-mid: #5d5d5d;
    --grey-light: #6e6e6e;
    --text-grey: #555555;
    --paper: #ffffff;
    --backdrop: #e9e9e9;
    --soft-white: #eeeeee;
  }
  * { box-sizing: border-box; margin: 0; padding: 0; }
  html, body { width: 1200px; height: 963px; overflow: hidden; }
  body {
    background: var(--backdrop);
    font-family: "Lato", sans-serif;
    display: flex;
    flex-direction: column;
    align-items: center;
    justify-content: center;
    gap: 56px;
  }
  .card {
    position: relative;
    width: 640px;
    height: 366px;
    overflow: hidden;
    box-shadow: 0 6px 18px rgba(0,0,0,0.18);
  }

  /* Front */
  .card-front { background: var(--paper); }
  .brand {
    position: absolute;
    display: flex;
    align-items: center;
    gap: 14px;
  }
  .brand-mark {
    width: 34px; height: 34px;
    background: var(--orange);
    flex: none;
  }
  .brand-rule {
    width: 2px; height: 58px;
    background: var(--orange);
    flex: none;
  }
  .brand-text { display: flex; flex-direction: column; gap: 4px; white-space: nowrap; }
  .brand-name {
    font-family: "Montserrat", sans-serif;
    font-weight: 600;
    color: var(--orange);
    letter-spacing: 0.5px;
    text-transform: uppercase;
  }
  .brand-phone { color: var(--orange); letter-spacing: 1px; }
  .card-front .brand { top: 34px; left: 40px; }
  .card-front .brand-name { font-size: 15px; }
  .card-front .brand-phone { font-size: 12px; }

  .divider {
    position: absolute;
    top: 132px; left: 40px; right: 40px;
    height: 1.5px;
    background: var(--orange);
  }
  .contact-list {
    position: absolute;
    top: 148px; left: 40px;
    list-style: none;
    font-size: 13px;
    color: var(--text-grey);
    line-height: 1.65;
  }
  .contact-list li { display: flex; align-items: center; gap: 8px; white-space: nowrap; }
  .contact-list svg { width: 11px; height: 11px; fill: var(--orange); flex: none; }
  .contact-list .abn-tag { color: var(--orange); font-weight: 700; font-size: 10px; width: 11px; flex: none; }
  .accent { color: var(--orange); }

  .person {
    position: absolute;
    top: 170px; right: 40px;
    text-align: right;
  }
  .person-name {
    font-size: 28px;
    font-weight: 400;
    color: var(--orange);
    letter-spacing: 1px;
    text-transform: uppercase;
    white-space: nowrap;
  }
  .person-role { font-size: 15px; color: var(--text-grey); margin-top: 2px; }
  .address {
    position: absolute;
    top: 252px; right: 40px;
    text-align: right;
    font-size: 14px;
    color: var(--text-grey);
    line-height: 1.35;
  }
  .address .suburb { color: var(--orange); }
  .front-band { position: absolute; left: 0; bottom: 0; width: 640px; height: 90px; }

  /* Back */
  .card-back {
    background: linear-gradient(135deg, var(--grey-dark) 0%, var(--grey-light) 60%, var(--grey-mid) 100%);
  }
  .card-back .brand {
    top: 120px; left: 50%;
    transform: translateX(-50%);
    gap: 18px;
  }
  .card-back .brand-mark { width: 52px; height: 52px; }
  .card-back .brand-rule { height: 84px; }
  .card-back .brand-name { font-size: 21px; }
  .card-back .brand-phone { font-size: 16px; }
  .web {
    position: absolute;
    bottom: 70px; left: 0; right: 0;
    text-align: center;
    font-size: 15px;
    color: var(--soft-white);
    letter-spacing: 0.3px;
  }
</style>
</head>
<body>

  <section class="card card-front">
    <div class="brand">
      <div class="brand-mark"></div>
      <div class="brand-rule"></div>
      <div class="brand-text">
        <span class="brand-name">Holloway Paving Service</span>
        <span class="brand-phone">0418259730</span>
      </div>
    </div>

    <div class="divider"></div>

    <ul class="contact-list">
      <li><svg viewBox="0 0 12 12"><path d="M3 1l2 2.5-1.2 1.3a7 7 0 0 0 3.4 3.4L8.5 7 11 9l-1.2 2C5 11 1 7 1 2.2z"/></svg><span>+61 418 259 730</span></li>
      <li><svg viewBox="0 0 12 12"><path d="M1 3h10v6H1zm1 .8v.4l4 2.6 4-2.6v-.4z"/></svg><span>markholloway@brightmail.com.au</span></li>
      <li><svg viewBox="0 0 12 12"><circle cx="6" cy="6" r="5"/></svg><span>www.<span class="accent">hollowaypaving</span>.com.au</span></li>
      <li><span class="abn-tag">#</span><span>ABN 62318470915</span></li>
    </ul>

    <div class="person">
      <div class="person-name">Mark Holloway</div>
      <div class="person-role">Director</div>
    </div>

    <div class="address">
      <div class="suburb">Brookvale</div>
      <div>Ashford, Tasmania 7190</div>
    </div>

    <svg class="front-band" viewBox="0 0 640 90" preserveAspectRatio="none" aria-hidden="true">
      <path d="M0 22 L250 60 L0 30 Z" fill="#6a6a6a"/>
      <path d="M0 34 L260 62 C300 66 320 72 350 90 L0 90 Z" fill="#ec6a1f"/>
      <path d="M300 70 C360 66 420 62 640 58 L640 90 L350 90 C330 80 320 74 300 70 Z" fill="#ec6a1f"/>
    </svg>
  </section>

  <section class="card card-back">
    <div class="brand">
      <div class="brand-mark"></div>
      <div class="brand-rule"></div>
      <div class="brand-text">
        <span class="brand-name">Holloway Paving Service</span>
        <span class="brand-phone">0418259730</span>
      </div>
    </div>
    <p class="web">www.<span class="accent">hollowaypaving</span>.com.au</p>
  </section>

</body>
</html>
```